Business Card Design - ChoiceCraft

Looking for creative, modern design, two sided for ChoiceCraft that is consistent with color and feel of website www.choicecraftpro.net.
Updates

Back of card will be used to promote products or have a quote revolving around decisions, change, leadership, innovation, creativity. Back should also have space to promote website, but optional to use the icon. Front of the card will need to use the icon and have standard place for name, job title, phone and email. We are not looking to put a mailing address or fax. Also want space to place a few words/phrase explaining what we do...such as individual growth and organizational development or tools, training, information...in addition, want the facebook icon small on the front somewhere as we are also on facebook.

Vector file uploaded of icon.

Target Market(s)

Professional coaching for individual growth and organizational development

Industry/Entity Type

Business

Requirements
Must have
• Icon...see attached.

```html
<!DOCTYPE html>
<html lang="en">
<head>
<meta charset="utf-8">
<title>ChoiceCraft Business Card</title>
<link rel="stylesheet" href="https://fonts.googleapis.com/css2?family=PT+Sans&family=Tinos:wght@400;700&family=Arimo:wght@400;700&display=swap">
<style>
  :root {
    --page-bg: #2a2a2a;
    --card-bg: #ffffff;
    --ink: #3a3a3a;
    --ink-soft: #555555;
    --brand-blue: #1a86c8;
    --brand-blue-light: #35b4ea;
    --brand-blue-deep: #0f6fae;
    --mark-fill: #cfe3f3;
    --mark-ring: #4aa6dc;
    --on-blue: #ffffff;
  }
  * { box-sizing: border-box; margin: 0; padding: 0; }
  html, body { width: 1200px; height: 761px; overflow: hidden; }
  body {
    background: var(--page-bg);
    position: relative;
    font-family: "Arimo", Arial, sans-serif;
    color: var(--ink);
  }
  .card {
    position: absolute;
    top: 216px;
    width: 540px;
    height: 330px;
    background: var(--card-bg);
    border-radius: 24px;
    overflow: hidden;
  }
  .card--front { left: 45px; }
  .card--back { left: 615px; }

  /* Front */
  .brand {
    position: absolute; left: 36px; top: 30px;
    display: flex; align-items: center; gap: 18px;
  }
  .brand__mark {
    width: 84px; height: 84px; border-radius: 50%;
    background: var(--mark-fill); border: 6px solid var(--mark-ring);
  }
  .brand__name {
    font-family: "PT Sans", sans-serif;
    font-size: 30px; color: #111; letter-spacing: 0.3px;
  }
  .feature-mark {
    position: absolute; right: 42px; top: 118px;
    width: 104px; height: 104px; border-radius: 50%;
    background: var(--mark-fill); border: 8px solid var(--mark-ring);
    z-index: 2;
  }
  .identity {
    position: absolute; left: 62px; top: 150px;
    font-family: "Tinos", serif; color: var(--ink-soft);
  }
  .identity__name { font-size: 22px; font-weight: 700; }
  .identity__title { font-size: 17px; font-weight: 400; }
  .contacts {
    position: absolute; left: 62px; top: 188px;
    list-style: none;
    font-family: "Tinos", serif; font-size: 15px; color: var(--ink-soft);
    line-height: 19px;
  }
  .contacts li { display: flex; align-items: center; gap: 6px; }
  .contacts svg { width: 11px; height: 11px; flex: none; }
  .contacts .social-box {
    width: 10px; height: 10px; background: var(--brand-blue); flex: none;
  }
  .band {
    position: absolute; left: 0; bottom: 0; width: 540px; height: 110px;
  }
  .tagline {
    position: absolute; left: 40px; bottom: 14px;
    font-family: "Tinos", serif; font-size: 15px; color: var(--on-blue);
  }

  /* Back */
  .quotes {
    position: absolute; left: 32px; top: 26px; right: 24px;
    list-style: none; font-size: 15px; color: var(--ink);
  }
  .quote { margin-bottom: 9px; }
  .quote__text { position: relative; padding-left: 16px; }
  .quote__text::before {
    content: "\201C"; position: absolute; left: 0; top: -6px;
    font-size: 24px; font-weight: 700; color: var(--ink);
  }
  .quote__text::after {
    content: "\201D"; font-size: 24px; font-weight: 700;
    vertical-align: -8px; margin-left: 2px;
  }
  .quote__author {
    padding-left: 22px; color: var(--brand-blue); font-weight: 700; font-size: 15px;
  }
  .quote__author span { color: var(--ink); font-weight: 400; }
  .back-mark {
    position: absolute; right: 40px; bottom: 28px;
    width: 108px; height: 108px; border-radius: 50%;
    background: #e4eef7; border: 8px solid #9fcbec;
  }
</style>
</head>
<body>
  <section class="card card--front" aria-label="Card front">
    <div class="brand">
      <div class="brand__mark" aria-hidden="true"></div>
      <span class="brand__name">ChoiceCraft</span>
    </div>
    <div class="feature-mark" aria-hidden="true"></div>

    <p class="identity">
      <span class="identity__name">Your Name,</span>
      <span class="identity__title">Title</span>
    </p>
    <ul class="contacts">
      <li>
        <svg viewBox="0 0 12 12" aria-hidden="true"><path d="M3 1 L5 3.5 L4 5 Q5 7.5 7 8 L8.5 7 L11 9 L9.5 11 Q4 10.5 1 3 Z" fill="#555"/></svg>
        123-456-789
      </li>
      <li>
        <svg viewBox="0 0 12 12" aria-hidden="true"><rect x="1" y="3" width="10" height="7" fill="none" stroke="#555" stroke-width="1.3"/><path d="M1 3 L6 7 L11 3" fill="none" stroke="#555" stroke-width="1.3"/></svg>
        info@choicecraftpro.net
      </li>
      <li>
        <svg viewBox="0 0 12 12" aria-hidden="true"><circle cx="6" cy="6" r="5" fill="none" stroke="#555" stroke-width="1.2"/><ellipse cx="6" cy="6" rx="2.2" ry="5" fill="none" stroke="#555" stroke-width="1"/><path d="M1 6 H11" stroke="#555" stroke-width="1"/></svg>
        www.choicecraftpro.net
      </li>
      <li>
        <span class="social-box" aria-hidden="true"></span>
        /choicecraftpro
      </li>
    </ul>

    <svg class="band" viewBox="0 0 540 110" preserveAspectRatio="none" aria-hidden="true">
      <path d="M0 78 L340 70 Q420 68 470 40 Q505 22 540 20 L540 110 L0 110 Z" fill="var(--brand-blue-light)"/>
      <path d="M0 82 L360 76 Q440 74 490 48 Q515 36 540 34 L540 110 L0 110 Z" fill="var(--brand-blue)"/>
    </svg>
    <p class="tagline">Supporting individual growth and organizational development.</p>
  </section>

  <section class="card card--back" aria-label="Card back">
    <ul class="quotes">
      <li class="quote">
        <p class="quote__text">Try not to become a man of success, but rather a man of value.</p>
        <p class="quote__author"><span>-</span> Alden Marsh</p>
      </li>
      <li class="quote">
        <p class="quote__text">The only constant is change.</p>
        <p class="quote__author"><span>-</span> Heron Vale</p>
      </li>
      <li class="quote">
        <p class="quote__text">We are what we repeatedly do. Excellence is not an act, it is a habit.</p>
        <p class="quote__author"><span>-</span> Arlo Stein</p>
      </li>
      <li class="quote">
        <p class="quote__text">Simplicity is the ultimate sophistication.</p>
        <p class="quote__author"><span>-</span> Leon Davies</p>
      </li>
      <li class="quote">
        <p class="quote__text">Life is not fair - get used to it.</p>
        <p class="quote__author"><span>-</span> Bill Garner</p>
      </li>
    </ul>
    <div class="back-mark" aria-hidden="true"></div>
  </section>
</body>
</html>
```